Landscape design build company door flyer

I would like this flyer to convey a high-level of professionalism for a company that is excellent with communication with their clients as well as a company that does incredible installations

Went on vacation/holiday

```html
<!DOCTYPE html>
<html lang="en">
<head>
<meta charset="utf-8">
<title>Cedarline Builders – Flyer</title>
<link href="https://fonts.googleapis.com/css2?family=Montserrat:wght@500;600;700;800&family=Roboto:wght@900&display=swap" rel="stylesheet">
<style>
:root{
  --page:#ececec;
  --paper:#e6e6e6;
  --navy:#0c2a3f;
  --ink:#15212b;
  --orange:#f26e0b;
  --accent:#f5a51f;
  --white:#ffffff;
}
*{margin:0;padding:0;box-sizing:border-box}
html,body{width:1200px;height:1029px;overflow:hidden;background:var(--page)}
.flyer{position:absolute;left:212px;top:14px;width:776px;height:1000px;background:var(--paper);overflow:hidden;font-family:"Montserrat",sans-serif;color:var(--ink)}
.hero{position:absolute;left:0;top:0;width:776px;height:544px;
  background:linear-gradient(160deg,#3c5d8f 0%,#2f4c7a 30%,#5a6470 55%,#6f8a55 78%,#4f7a36 100%)}
.brand-panel{position:absolute;left:0;top:0;width:420px;height:170px}
.brand-name{position:absolute;left:0;top:72px;width:342px;text-align:center;font-family:"Montserrat",sans-serif;font-weight:700;font-size:21px;line-height:26px;color:var(--navy);letter-spacing:.3px}
.gallery-photo{position:absolute;width:206px;height:206px;border-radius:50%;border:6px solid var(--white)}
.photo-pavilion{left:45px;top:418px;background:linear-gradient(170deg,#8b9bb0 0%,#9a6a3a 45%,#6b6b70 75%,#5f8a3a 100%)}
.photo-cabin{left:286px;top:418px;background:linear-gradient(180deg,#3d5a3c 0%,#4c6b45 35%,#b8632f 60%,#6aa540 100%)}
.photo-steps{left:525px;top:418px;background:linear-gradient(170deg,#b8b1a3 0%,#9a7150 35%,#8a5f3c 70%,#c2ae8f 100%)}
.section-title{position:absolute;top:652px;font-weight:800;font-size:25px;color:var(--navy);letter-spacing:-.2px}
.section-title::after{content:"";position:absolute;left:0;top:34px;width:70px;height:3px;border-radius:2px;background:var(--accent)}
.about-title{left:38px}
.services-title{left:458px}
.about-text{position:absolute;left:37px;top:700px;width:352px;font-size:13.6px;line-height:15.8px;text-align:justify;font-weight:500;color:var(--ink);hyphens:auto;-webkit-hyphens:auto}
.services-list{position:absolute;left:456px;top:700px;list-style:none}
.services-list li{display:flex;align-items:center;height:22.5px;font-size:15.4px;font-weight:600;color:var(--ink)}
.services-list svg{width:14px;height:14px;margin-right:16px}
.contact-band{position:absolute;left:0;top:900px;width:776px;height:100px}
.phone-icon{position:absolute;left:37px;top:926px;width:51px;height:51px;background:var(--orange);display:flex;align-items:center;justify-content:center}
.phone-number{position:absolute;left:99px;top:922px;font-family:"Roboto",sans-serif;font-weight:900;font-size:45px;color:var(--white);letter-spacing:-.5px;line-height:56px}
.contact-line{position:absolute;left:508px;display:flex;align-items:center;font-size:15px;font-weight:500;color:var(--white)}
.contact-line svg{width:17px;height:17px;margin-right:18px}
.contact-email{top:920px}
.contact-web{top:946px}
</style>
</head>
<body>
<main class="flyer">
  <div class="hero" role="img" aria-label="Photo of a blue house with a new two-level deck, dark railings and grey composite stairs over a concrete pad"></div>

  <svg class="brand-panel" viewBox="0 0 420 170" aria-hidden="true">
    <polygon points="0,0 407,0 321,170 0,170" fill="var(--paper)"/>
  </svg>
  <div class="brand-name">Cedarline Builders</div>

  <div class="gallery-photo photo-pavilion" role="img" aria-label="Photo of a timber pavilion over a stone outdoor kitchen"></div>
  <div class="gallery-photo photo-cabin" role="img" aria-label="Photo of a wraparound cedar deck on a cabin among tall trees"></div>
  <div class="gallery-photo photo-steps" role="img" aria-label="Photo of wide composite deck steps"></div>

  <h2 class="section-title about-title">ABOUT US</h2>
  <p class="about-text">Discover the endless possibilities for your outdoor space with The Cedarline Builders Team. Our team of skilled artisans is dedicated to turning your outdoor space into a breathtaking oasis that you’ll love coming home to. Whether it’s a cozy patio for intimate gatherings, a sprawling deck to host memorable parties, or a custom paver driveway that adds instant curb appeal, our high-quality craftsmanship ensures stunning results that exceed your expectations.</p>

  <h2 class="section-title services-title">OUR SERVICES</h2>
  <ul class="services-list">
    <li><svg viewBox="0 0 14 14"><circle cx="7" cy="7" r="7" fill="var(--orange)"/><path d="M3.8 7.2l2.2 2.2 4.2-4.4" stroke="#fff" stroke-width="1.8" fill="none" stroke-linecap="round" stroke-linejoin="round"/></svg>Paver Patios</li>
    <li><svg viewBox="0 0 14 14"><circle cx="7" cy="7" r="7" fill="var(--orange)"/><path d="M3.8 7.2l2.2 2.2 4.2-4.4" stroke="#fff" stroke-width="1.8" fill="none" stroke-linecap="round" stroke-linejoin="round"/></svg>Paver Driveways</li>
    <li><svg viewBox="0 0 14 14"><circle cx="7" cy="7" r="7" fill="var(--orange)"/><path d="M3.8 7.2l2.2 2.2 4.2-4.4" stroke="#fff" stroke-width="1.8" fill="none" stroke-linecap="round" stroke-linejoin="round"/></svg>Retaining Walls</li>
    <li><svg viewBox="0 0 14 14"><circle cx="7" cy="7" r="7" fill="var(--orange)"/><path d="M3.8 7.2l2.2 2.2 4.2-4.4" stroke="#fff" stroke-width="1.8" fill="none" stroke-linecap="round" stroke-linejoin="round"/></svg>Decks &amp; Railings</li>
    <li><svg viewBox="0 0 14 14"><circle cx="7" cy="7" r="7" fill="var(--orange)"/><path d="M3.8 7.2l2.2 2.2 4.2-4.4" stroke="#fff" stroke-width="1.8" fill="none" stroke-linecap="round" stroke-linejoin="round"/></svg>Pools</li>
    <li><svg viewBox="0 0 14 14"><circle cx="7" cy="7" r="7" fill="var(--orange)"/><path d="M3.8 7.2l2.2 2.2 4.2-4.4" stroke="#fff" stroke-width="1.8" fill="none" stroke-linecap="round" stroke-linejoin="round"/></svg>Outdoor Lighting</li>
    <li><svg viewBox="0 0 14 14"><circle cx="7" cy="7" r="7" fill="var(--orange)"/><path d="M3.8 7.2l2.2 2.2 4.2-4.4" stroke="#fff" stroke-width="1.8" fill="none" stroke-linecap="round" stroke-linejoin="round"/></svg>Firepits &amp; Fireplaces</li>
  </ul>

  <svg class="contact-band" viewBox="0 0 776 100" aria-hidden="true">
    <rect x="0" y="7" width="776" height="93" fill="var(--navy)"/>
    <polygon points="473,0 776,0 776,100 432,100" fill="var(--orange)"/>
  </svg>
  <div class="phone-icon">
    <svg width="30" height="30" viewBox="0 0 24 24" aria-hidden="true"><path fill="#fff" d="M6.6 10.8a15.1 15.1 0 0 0 6.6 6.6l2.2-2.2c.3-.3.7-.4 1-.2 1.1.4 2.3.6 3.6.6.6 0 1 .4 1 1V20c0 .6-.4 1-1 1A17 17 0 0 1 3 4c0-.6.4-1 1-1h3.5c.6 0 1 .4 1 1 0 1.3.2 2.5.6 3.6.1.3 0 .7-.2 1z"/></svg>
  </div>
  <div class="phone-number">555-014-2398</div>
  <div class="contact-line contact-email">
    <svg viewBox="0 0 24 24" aria-hidden="true"><rect x="2" y="5" width="20" height="14" fill="#fff"/><path d="M2 5l10 8 10-8" stroke="var(--orange)" stroke-width="2" fill="none"/></svg>
    hello@cedarlinebuilders.com
  </div>
  <div class="contact-line contact-web">
    <svg viewBox="0 0 24 24" aria-hidden="true" fill="none" stroke="#fff" stroke-width="1.6"><circle cx="12" cy="12" r="9"/><ellipse cx="12" cy="12" rx="4" ry="9"/><path d="M3 12h18M5 7.5h14M5 16.5h14"/></svg>
    www.cedarlinebuilders.com
  </div>
</main>
</body>
</html>
```